Header Card Design for Marine Tool Product

We package up our small tools in bags. A nice header card would finish the look.
* Bag is 4" wide. Header Card should be 4x4, folded to 4x2
* Back of card should have 2.25x1.25 area for our part number sticker.
* Design to reinforce the brand and add (perception of) quality to the product.

Brand Website: harbolvex.com

Target Market(s)

Boat Mechanics/Boat owners

Industry/Entity Type

```html
<!DOCTYPE html>
<html lang="en">
<head>
<meta charset="utf-8">
<title>Harbolvex Header Card</title>
<link href="https://fonts.googleapis.com/css2?family=Montserrat:ital,wght@0,500;0,600;0,800;1,700&display=swap" rel="stylesheet">
<style>
  :root {
    --ink: #0f3a47;
    --teal: #45737a;
    --paper: #ffffff;
    --stage: #f2f2f2;
    --fold: #9a9a9a;
  }
  html, body {
    margin: 0;
    width: 1200px;
    height: 840px;
    overflow: hidden;
    background: var(--stage);
    font-family: "Montserrat", Arial, sans-serif;
  }
  .header-card {
    position: absolute;
    left: 300px;
    top: 120px;
    width: 600px;
    height: 600px;
  }
  .card-edge { fill: var(--paper); stroke: var(--fold); stroke-width: 2; }
  .fold-line { stroke: var(--fold); stroke-width: 3; }
  .hang-hole { fill: var(--paper); stroke: var(--ink); stroke-width: 2; }
  .sticker-area { fill: none; stroke: var(--ink); stroke-width: 3.5; }
  .brand-name { font-family: "Montserrat", Arial, sans-serif; font-weight: 800; fill: var(--ink); }
  .brand-mark { fill: var(--ink); }
  .contact-line { font-family: "Montserrat", Arial, sans-serif; font-weight: 500; font-size: 21px; fill: var(--ink); }
  .contact-name { font-weight: 800; font-size: 21px; fill: var(--ink); font-family: "Montserrat", Arial, sans-serif; }
  .tagline { font-family: "Montserrat", Arial, sans-serif; font-style: italic; font-weight: 700; font-size: 35px; fill: var(--ink); }
  .tag-icon { fill: none; stroke: var(--teal); stroke-width: 2.2; stroke-linecap: round; }
</style>
</head>
<body>
<svg class="header-card" viewBox="0 0 910 910" role="group" aria-label="Header card, folding 4 by 4 inch, back panel above, front panel below">
  <defs>
    <linearGradient id="decor-fill" x1="0" y1="0" x2="1" y2="1">
      <stop offset="0" stop-color="#45737a"/>
      <stop offset="1" stop-color="#0f3a47"/>
    </linearGradient>
    <clipPath id="card-clip"><rect x="0" y="0" width="910" height="910"/></clipPath>
  </defs>

  <rect class="card-edge" x="1" y="1" width="908" height="908"/>

  <!-- back panel (prints upside down so it reads correctly after folding) -->
  <g class="back-panel">
    <rect class="sticker-area" x="369" y="28" width="513" height="285" rx="14"/>
    <path class="hang-hole" d="M371,344 H540 A26,26 0 0 1 540,396 H488 A33,33 0 0 1 422,396 H371 A26,26 0 0 1 371,344 Z"/>
    <g transform="rotate(180 455 227.5)">
      <rect class="brand-mark" x="586" y="108" width="54" height="54"/>
      <text class="brand-name" x="654" y="150" font-size="30">HARBOLVEX</text>
      <text class="contact-name" x="586" y="226">HARBOLVEX</text>
      <text class="contact-line" x="586" y="256">418 Keelson Ave,</text>
      <text class="contact-line" x="586" y="285">Suite 12,</text>
      <text class="contact-line" x="586" y="315">Port Alden SC, 29077,</text>
      <text class="contact-line" x="586" y="353">www.harbolvex.com</text>
      <text class="contact-line" x="586" y="382">Tel: (555)214-0387</text>
    </g>
  </g>

  <line class="fold-line" x1="0" y1="455" x2="910" y2="455"/>

  <!-- front panel -->
  <g class="front-panel">
    <path class="hang-hole" d="M371,514 H422 A33,33 0 0 1 488,514 H540 A26.5,26.5 0 0 1 540,567 H371 A26.5,26.5 0 0 1 371,514 Z"/>

    <rect class="brand-mark" x="44" y="600" width="104" height="104"/>
    <text class="brand-name" x="172" y="672" font-size="50">HARBOLVEX</text>

    <rect x="594" y="494" width="316" height="416" fill="url(#decor-fill)" clip-path="url(#card-clip)" role="img" aria-label="Large brand decoration in dark and mid teal"/>

    <g class="tag-icon" transform="translate(68 764)">
      <rect x="-12" y="-2" width="14" height="8" rx="4" transform="rotate(-45)"/>
      <rect x="-2" y="-2" width="14" height="8" rx="4" transform="rotate(-45)"/>
    </g>
    <text class="tagline" x="96" y="778">Super Tough</text>

    <g class="tag-icon" transform="translate(68 813)">
      <circle r="14"/>
      <circle r="9"/>
      <path d="M0,-5 V0 H4 M-3,-17 H3"/>
    </g>
    <text class="tagline" x="96" y="826">Time-Saving</text>

    <g class="tag-icon" transform="translate(68 860)">
      <circle cy="-2" r="9"/>
      <path d="M-4,8 H4 M-3,12 H3 M0,-19 V-15 M-15,-2 H-19 M15,-2 H19 M-11,-13 L-14,-16 M11,-13 L14,-16"/>
    </g>
    <text class="tagline" x="96" y="874">Innovative Design</text>
  </g>
</svg>
</body>
</html>
```